Brindle Yard Care. The best in the biz

I run a lawn care service that offers full service mowing. 100% satisfaction guarantee. Fast, Friendly, quality service "I am your lawns best friend" I cut residential lawns. I offer a mow package that includes trimming, edging and clean up. Prices very from 20 dollars to 75. I want my logo to stand out. Free estimates

Target Market(s)

Home owners

Industry/Entity Type

Landscaping

Contact Information for Business Card

555-812-4473 tomvale48@quillmail.net Derek. Brindle Yard care

Colors
f37122
9bcb3c
cadf82

Requirements
Must have
• Company name.
• Phone number
• Email
• My services
• images
Nice to have
• A sun that is growing grass.
Should not have
• Incorrect information

```html
<!DOCTYPE html>
<html lang="en">
<head>
<meta charset="utf-8">
<title>Brindle Yard Care – Business Cards</title>
<link href="https://fonts.googleapis.com/css2?family=Open+Sans:ital,wght@0,400;0,600;0,700;1,700&display=swap" rel="stylesheet">
<style>
  :root {
    --backdrop: #2c2e31;
    --card: #ffffff;
    --green: #1f9a3e;
    --ink: #1a1a1a;
    --sun-soft: #fbf0bd;
    --leaf-soft: #d6ede0;
  }
  * { box-sizing: border-box; margin: 0; padding: 0; }
  html, body {
    width: 1200px; height: 864px; overflow: hidden;
    background: var(--backdrop);
    font-family: "Open Sans", Arial, sans-serif;
  }
  .card {
    position: absolute;
    width: 600px; height: 343px;
    background: var(--card);
    overflow: hidden;
  }
  .card--front { left: 300px; top: 50px; }
  .card--back  { left: 300px; top: 460px; }

  .brand-name {
    color: var(--green);
    font-weight: 700;
    letter-spacing: 1px;
    white-space: nowrap;
    display: flex; align-items: center; gap: 12px;
  }
  .brand-dot {
    width: 26px; height: 26px; border-radius: 50%;
    background: var(--green);
    flex: none;
  }

  /* front */
  .card--front .brand-name {
    position: absolute; left: 0; right: 0; top: 92px;
    justify-content: center; font-size: 44px;
  }
  .rule { position: absolute; height: 2px; background: var(--green); }
  .card--front .rule--left  { left: 0; top: 192px; width: 100px; }
  .card--front .rule--right { right: 0; top: 206px; width: 95px; }
  .guarantee {
    position: absolute; left: 0; right: 0; top: 180px;
    text-align: center; color: var(--green);
    font-style: italic; font-weight: 700; font-size: 22px;
  }
  .service-points {
    position: absolute; left: 0; right: 0; top: 230px;
    text-align: center; color: var(--ink);
    font-weight: 700; font-size: 15px; word-spacing: 3px;
  }

  /* back */
  .sun-decor {
    position: absolute; right: 18px; top: 60px;
    width: 250px; height: 250px;
  }
  .card--back .brand-name {
    position: absolute; left: 34px; top: 28px; font-size: 36px;
  }
  .person {
    position: absolute; left: 60px; top: 120px;
    color: var(--green); font-weight: 700; font-size: 19px;
  }
  .contact {
    position: absolute; left: 46px; top: 170px;
    list-style: none; color: var(--ink); font-size: 14px;
  }
  .contact li { display: flex; align-items: center; gap: 8px; line-height: 26px; }
  .contact svg { width: 13px; height: 13px; fill: var(--green); }
  .card--back .rule--left  { left: 0; top: 245px; width: 150px; }
  .card--back .rule--right { right: 0; top: 320px; width: 170px; }
  .motto {
    position: absolute; left: 160px; top: 260px;
    color: var(--ink); font-weight: 700; font-size: 20px;
  }
</style>
</head>
<body>

<section class="card card--front">
  <div class="brand-name"><span class="brand-dot"></span>Brindle Yard Care</div>
  <span class="rule rule--left"></span>
  <p class="guarantee">100% satisfaction guarantee.</p>
  <span class="rule rule--right"></span>
  <p class="service-points">Fast | Friendly | Quality Service</p>
</section>

<section class="card card--back">
  <svg class="sun-decor" viewBox="0 0 250 250" aria-hidden="true">
    <circle cx="125" cy="125" r="110" fill="var(--sun-soft)" opacity="0.8"/>
  </svg>
  <div class="brand-name"><span class="brand-dot"></span>Brindle Yard Care</div>
  <p class="person">Derek</p>
  <ul class="contact">
    <li>
      <svg viewBox="0 0 24 24"><path d="M6.6 10.8a15.1 15.1 0 0 0 6.6 6.6l2.2-2.2c.3-.3.7-.4 1-.2 1.1.4 2.3.6 3.6.6.6 0 1 .4 1 1V20c0 .6-.4 1-1 1A17 17 0 0 1 3 4c0-.6.4-1 1-1h3.5c.6 0 1 .4 1 1 0 1.3.2 2.5.6 3.6.1.3 0 .7-.2 1z"/></svg>
      555-812-4473
    </li>
    <li>
      <svg viewBox="0 0 24 24"><path d="M2 5h20v14H2zm2 2v.5l8 5 8-5V7zm0 2.8V17h16V9.8l-8 5z"/></svg>
      tomvale48@quillmail.net
    </li>
  </ul>
  <span class="rule rule--left"></span>
  <p class="motto">I am your lawns best friend</p>
  <span class="rule rule--right"></span>
</section>

</body>
</html>
```